business card

Business card for new business.
Red and black corporate colors.
Card can have an Indsutrial feel to it. Feel free to add Rust, Bolted steel, or graphics as you see fit. We provide highly specialized services to the below mentioned industries.
Keep information out of corners so that if I want I can choose rounded corners.
Information
- front. name - title - phone - email
- Rear
Refining - Rail - Infrastructure - Mining - Energy
Calgary - Edmonton - Fort McMurray - Revelstoke - Vancouver

```html
<!DOCTYPE html>
<html lang="en">
<head>
<meta charset="utf-8">
<title>Girderline Business Card</title>
<link rel="stylesheet" href="https://fonts.googleapis.com/css2?family=Roboto:wght@400;700&family=Roboto+Condensed:wght@700&display=swap">
<style>
  :root {
    --backdrop: #262626;
    --card-white: #f3f3f3;
    --brand-red: #e50019;
    --steel-grey: #808080;
    --logo-grey: #7a7a7a;
    --text-white: #ffffff;
  }
  html, body {
    margin: 0;
    padding: 0;
    width: 1200px;
    height: 960px;
    overflow: hidden;
    background: var(--backdrop);
  }
  .canvas {
    position: relative;
    width: 1200px;
    height: 960px;
  }
  .card {
    position: absolute;
    width: 600px;
    height: 343px;
    box-sizing: border-box;
  }
  .card-front {
    left: 314px;
    top: 113px;
    background: var(--card-white);
  }
  .front-frame {
    position: absolute;
    left: 15px;
    top: 14px;
    width: 571px;
    height: 317px;
    box-sizing: border-box;
    border: 2px solid var(--brand-red);
  }
  .brand {
    position: absolute;
    left: 0;
    right: 0;
    top: 72px;
    display: flex;
    justify-content: center;
    align-items: center;
    gap: 14px;
  }
  .brand-mark {
    width: 22px;
    height: 22px;
    background: var(--brand-red);
  }
  .brand-name {
    font-family: "Roboto Condensed", sans-serif;
    font-weight: 700;
    font-size: 54px;
    line-height: 1;
    color: var(--logo-grey);
    letter-spacing: 1px;
  }
  .info-band {
    position: absolute;
    left: 15px;
    top: 206px;
    width: 571px;
    height: 125px;
    background: var(--brand-red);
    color: var(--text-white);
    font-family: "Roboto", sans-serif;
    text-align: center;
  }
  .person {
    margin-top: 16px;
    line-height: 1;
  }
  .person-name {
    font-family: "Roboto Condensed", sans-serif;
    font-weight: 700;
    font-size: 23px;
  }
  .person-title {
    font-size: 15px;
  }
  .contact {
    margin-top: 6px;
    font-size: 14.5px;
  }
  .divider {
    width: 420px;
    height: 1px;
    margin: 8px auto 9px;
    background: linear-gradient(to right, transparent, rgba(255,255,255,0.45), transparent);
  }
  .details {
    font-size: 14.5px;
    line-height: 18px;
  }
  .card-back {
    left: 311px;
    top: 472px;
    background: var(--steel-grey);
    display: flex;
    justify-content: center;
    align-items: center;
  }
  .back-name {
    font-family: "Roboto Condensed", sans-serif;
    font-weight: 700;
    font-size: 60px;
    color: var(--brand-red);
    letter-spacing: 1px;
  }
</style>
</head>
<body>
<main class="canvas">
  <section class="card card-front" aria-label="Business card front">
    <div class="front-frame"></div>
    <div class="brand">
      <span class="brand-mark" aria-hidden="true"></span>
      <span class="brand-name">GIRDERLINE</span>
    </div>
    <div class="info-band">
      <div class="person">
        <span class="person-name">DANIEL REYES -</span>
        <span class="person-title">CEO/FOUNDER</span>
      </div>
      <div class="contact">555 014 2290 | info@girderline.com | www.girderline.com</div>
      <div class="divider"></div>
      <div class="details">
        Welding • Piping • Fabrication • Heavy Lifting<br>
        Ashford • Brennan • Fort Kelsey • Redmoor • Lakeshore
      </div>
    </div>
  </section>

  <section class="card card-back" aria-label="Business card back">
    <span class="back-name">GIRDERLINE</span>
  </section>
</main>
</body>
</html>
```